Coastline Premier Retreats Business Card Design

Design a business card for Coastline Premier Retreats. Look at the website for colors and reference. Card should have logo, name, title, office number, mobile number, email, URL and a tagline like, "Luxury Hotel & Resort Email Marketing" (This might change).

https://www.coastlinepremierretreats.example

The rest I will leave up to your imagination.

Contact Information for Business Card

Logo, name, title, office number, mobile number, email, URL and a tagline like, "Luxury Hotel & Resort Email Marketing" (This might change).

```html
<!DOCTYPE html>
<html lang="en">
<head>
<meta charset="utf-8">
<title>Coastline Premier Retreats – Business Card</title>
<link href="https://fonts.googleapis.com/css2?family=Open+Sans:wght@400;600;700&display=swap" rel="stylesheet">
<style>
  :root {
    --page: #d9d2c6;
    --card-dark: #161414;
    --card-mid: #232121;
    --card-light: #353333;
    --orange: #c95c1e;
    --sand: #cdc2b2;
  }
  * { box-sizing: border-box; margin: 0; padding: 0; }
  html, body { width: 1200px; height: 1046px; overflow: hidden; }
  body {
    background: var(--page);
    font-family: "Open Sans", Arial, sans-serif;
    position: relative;
  }
  .card {
    position: absolute;
    left: 50px; top: 223px;
    width: 1100px; height: 600px;
    background: linear-gradient(90deg, var(--card-light) 0%, var(--card-mid) 30%, var(--card-dark) 60%, var(--card-mid) 100%);
    overflow: hidden;
    box-shadow: 0 10px 30px rgba(0,0,0,.25);
  }
  .card-curve { position: absolute; inset: 0; }
  .brand {
    position: absolute;
    left: 78px; top: 32px;
    height: 538px; width: 90px;
    display: flex; align-items: center; justify-content: center;
  }
  .brand-name {
    writing-mode: vertical-rl;
    transform: rotate(180deg);
    font-size: 34px;
    font-weight: 600;
    letter-spacing: 1px;
    color: var(--sand);
    white-space: nowrap;
  }
  .name-bar {
    position: absolute;
    right: 0; top: 44px;
    width: 27px; height: 92px;
    background: var(--orange);
  }
  .identity {
    position: absolute;
    right: 43px; top: 38px;
    text-align: right;
  }
  .person {
    font-size: 52px; font-weight: 700; line-height: 1.1;
    color: var(--sand);
  }
  .person .first { color: var(--orange); }
  .role {
    font-size: 28px; font-weight: 600; line-height: 1.3;
    color: var(--sand);
  }
  .tagline {
    position: absolute;
    right: 43px; top: 258px;
    text-align: right;
    font-size: 26px; font-weight: 400; line-height: 36px;
    color: var(--orange);
  }
  .contacts {
    position: absolute;
    right: 43px; top: 414px;
    list-style: none;
  }
  .contacts li {
    display: flex; align-items: center; justify-content: flex-end;
    height: 36px;
    font-size: 26px; color: var(--sand);
  }
  .contacts svg {
    width: 24px; height: 24px; margin-left: 20px; flex: none;
    fill: none; stroke: var(--orange); stroke-width: 2;
  }
</style>
</head>
<body>
  <div class="card">
    <svg class="card-curve" viewBox="0 0 1100 600" preserveAspectRatio="none" aria-hidden="true">
      <defs>
        <linearGradient id="curveShade" x1="0" y1="0" x2="1" y2="0">
          <stop offset="0" stop-color="#000" stop-opacity="0"/>
          <stop offset="1" stop-color="#000" stop-opacity="0.35"/>
        </linearGradient>
      </defs>
      <path d="M330 0 C 230 140, 230 420, 410 600 L 1100 600 L 1100 0 Z" fill="url(#curveShade)"/>
    </svg>

    <div class="brand"><span class="brand-name">Coastline Premier Retreats</span></div>

    <div class="name-bar"></div>
    <div class="identity">
      <p class="person"><span class="first">Marta</span> Kovarik</p>
      <p class="role">Managing Director</p>
    </div>

    <p class="tagline">Luxury Hotel &amp;<br>Resort Email Marketing</p>

    <ul class="contacts">
      <li>(555) 214-3860
        <svg viewBox="0 0 24 24"><path d="M5 3h4l2 5-2.5 1.5a11 11 0 0 0 6 6L16 13l5 2v4a2 2 0 0 1-2 2A16 16 0 0 1 3 5a2 2 0 0 1 2-2z"/></svg>
      </li>
      <li>(555) 482-1190
        <svg viewBox="0 0 24 24"><rect x="7" y="2" width="10" height="20" rx="2"/><line x1="11" y1="18" x2="13" y2="18"/></svg>
      </li>
      <li>www.coastlinepremierretreats.example
        <svg viewBox="0 0 24 24"><circle cx="12" cy="12" r="10"/><path d="M2 12h20M12 2c3 3 3 17 0 20M12 2c-3 3-3 17 0 20"/></svg>
      </li>
      <li>info@coastlinepremierretreats.example
        <svg viewBox="0 0 24 24"><rect x="2" y="5" width="20" height="15" rx="1"/><path d="M2 6l10 7 10-7"/></svg>
      </li>
    </ul>
  </div>
</body>
</html>
```